Exclusive beauty salon needs a price list or services booklet

I need a new very attractive flyer for my beauty salon, containing information on the different services and their prices.
In attachment you can find a pdf of the "old" one, but I'd love to have a beautifully designed new one!
I'd love to have a booklet in format 148 x 148 mm, or in US format, containing 12 or 16 pages, but if you can offer other nice looking designs they are welcome!
The services that need to come in the booklet with their prices can all be found on my website: www.atelierverano.be, starting with
Gelaatsverzorging
Wimperverlenging
Suikerontharing
Wimperlifting
Permanente Make Up
Airbrush Tanning

Target Market(s)

woman from 20 to 89 years old

Industry/Entity Type

Beauty Salon

Font styles to use
Sans Serif

Colors

Designer to choose colors to be used in the design.

Requirements
Must have
• a classy nice look, it must contain details about the services from my beauty salon and their prices, and nice pictures.
• The Names, prices and explanations of the services can easily be found on my website: www.atelierverano.be
Nice to have
• In attachment you can find the "old" price list in pdf, what I need now is a "new booklet" with the new logo and updated services price list.
• I need a very nice and attractive looking booklet, classy chique, Paris chique, looking very expensive.
Should not have
• Not too much colors, not too curly, but still feminine

```html
<!DOCTYPE html>
<html lang="nl">
<head>
<meta charset="utf-8">
<title>Airbrush Tanning – Prijslijst</title>
<link href="https://fonts.googleapis.com/css2?family=Source+Sans+3:ital,wght@0,400;1,400&display=swap" rel="stylesheet">
<style>
  :root {
    --frame-grey: #a7a8ab;
    --page-white: #ffffff;
    --accent-teal: #5bbdcc;
    --text-grey: #8a8a8d;
    --skin-light: #f1e6df;
    --skin-mid: #e9cdb9;
    --skin-tan: #e2a87f;
  }
  html, body {
    margin: 0;
    padding: 0;
    width: 1200px;
    height: 868px;
    overflow: hidden;
    background: var(--frame-grey);
  }
  .spread {
    position: absolute;
    left: 34px;
    top: 34px;
    width: 1132px;
    height: 800px;
    background: var(--page-white);
  }
  .service-info {
    position: absolute;
    left: 41px;
    top: 38px;
    width: 506px;
    font-family: "Source Sans 3", sans-serif;
  }
  .section-title {
    margin: 0 0 6px;
    font-weight: 400;
    font-size: 26px;
    line-height: 32px;
    color: var(--accent-teal);
  }
  .section-text {
    margin: 0 0 20px;
    font-style: italic;
    font-size: 17.5px;
    line-height: 23px;
    color: var(--text-grey);
    text-align: justify;
    hyphens: auto;
  }
  .price-line {
    position: absolute;
    left: 41px;
    top: 640px;
    width: 506px;
    margin: 0;
    font-family: "Source Sans 3", sans-serif;
    font-style: italic;
    font-size: 22px;
    color: var(--text-grey);
  }
  .price-line .price {
    margin-left: 22px;
    color: var(--accent-teal);
  }
  .tanning-photo {
    position: absolute;
    left: 588px;
    top: 0;
    width: 544px;
    height: 800px;
    background:
      linear-gradient(90deg, var(--skin-light) 0%, var(--skin-mid) 49%, var(--skin-tan) 51%, #dca07a 100%);
  }
</style>
</head>
<body>
  <main class="spread">
    <section class="service-info">
      <h2 class="section-title">De Airbrush Tanning Zelf</h2>
      <p class="section-text">Je huid wordt ingespoten met het product. Je ziet onmiddellijk het resultaat. Eventueel wordt in verschillende lagen gespoten zodat je zeker niet te bruin kan worden. Het inspuiten van het volledig lichaam duurt ongeveer 10 minuten. Daarna moet je alvorens de kleren aan te trekken nog een kwartiertje het product laten indrogen. Je verlaat het instituut met een mooie, gezonde bruine kleur.</p>
      <h2 class="section-title">De Nazorg</h2>
      <p class="section-text">Gedurende de eerste 8 uren na de airbrush tanning kan je best voorkomen om hevig te zweten. Dus best geen sport of andere zware inspanningen. Je mag niet douchen ! Tijdens deze eerste 8 uren kan het product een lichte kleur afgeven op kledij of lakens. Deze verdwijnt zonder probleem in de was. Na 8 uur mag je douchen. De tijdelijke kleurcomponent spoelt volledig weg. Ondertussen heeft je huid een mooie bruine kleur gekregen. Hoe beter je je huid hydrateert hoe langer je de kleur kan behouden. Je kleur blijft gemiddeld tussen de 7 dagen en 10 dagen naargelang je huidtype. Daarna begint de kleur te vervagen.</p>
    </section>
    <p class="price-line">Airbrush tanning van het volledige lichaam<span class="price">€29</span></p>
    <div class="tanning-photo" role="img" aria-label="Portretfoto van een vrouw, de ene helft van het gezicht licht, de andere helft gebruind na airbrush tanning"></div>
  </main>
</body>
</html>
```